BOLD & MINIMALIST DESIGN NEEDED

We want a very bold but minimalistic business card design that is impactful and utilizes both sides of the business card. Our current logo is included for your use.

We want bold fonts and good use of negative space. We don't want the logo to overpower the design.

Target Market(s)

Professionals who are building new commercial buildings.

Industry/Entity Type

Construction

Contact Information for Business Card

Name, Title, email, office phone, cell phone, website

Font styles to use
Serif
Sans Serif

Requirements
Must have
• Bold design!

```html
<!DOCTYPE html>
<html lang="en">
<head>
<meta charset="utf-8">
<title>Ridgeline Build – Business Card</title>
<link href="https://fonts.googleapis.com/css2?family=Montserrat:wght@400;600;800&display=swap" rel="stylesheet">
<style>
  :root {
    --backdrop: #959595;
    --card-light: #ffffff;
    --card-dark: #1e1e1e;
    --ink: #0d0d0d;
    --text-soft: #c4c4c4;
    --name-grey: #bdbdbd;
    --accent: #7dc84a;
  }
  * { margin: 0; padding: 0; box-sizing: border-box; }
  html, body {
    width: 1200px; height: 1200px; overflow: hidden;
    background: var(--backdrop);
    font-family: "Montserrat", sans-serif;
  }
  .card {
    position: absolute; left: 179px; width: 861px; height: 496px;
  }
  .card-front { top: 84px; background: var(--card-light); }
  .card-back { top: 621px; background: var(--card-dark); }

  .brand {
    position: absolute; display: flex; align-items: center; gap: 14px;
  }
  .brand-front {
    left: 0; right: 0; top: 0; bottom: 0; justify-content: center;
  }
  .brand-mark { width: 30px; height: 30px; background: var(--accent); }
  .brand-name {
    font-weight: 800; font-size: 46px; letter-spacing: 1px;
    color: var(--ink);
  }

  .person { position: absolute; left: 41px; top: 42px; }
  .person-name {
    font-weight: 600; font-size: 36px; color: var(--name-grey);
    letter-spacing: 0.5px; line-height: 1.1;
  }
  .person-title {
    font-weight: 400; font-size: 30px; color: var(--accent);
    letter-spacing: 1px; line-height: 1.2;
  }

  .contacts { position: absolute; left: 41px; top: 318px; list-style: none; }
  .contacts li {
    display: flex; align-items: center; height: 34.5px;
    font-size: 23px; color: var(--text-soft); letter-spacing: 1px;
  }
  .contacts svg { width: 26px; height: 26px; margin-right: 14px; fill: var(--accent); }
  .contacts .hl { color: var(--accent); }

  .brand-back { right: 40px; bottom: 40px; }
  .brand-back .brand-name { color: #ffffff; font-size: 30px; }
  .brand-back .brand-mark { width: 22px; height: 22px; }
</style>
</head>
<body>
  <section class="card card-front">
    <div class="brand brand-front">
      <span class="brand-mark"></span>
      <span class="brand-name">RIDGELINE BUILD</span>
    </div>
  </section>

  <section class="card card-back">
    <div class="person">
      <p class="person-name">Name Surename</p>
      <p class="person-title">Director</p>
    </div>

    <ul class="contacts">
      <li>
        <svg viewBox="0 0 24 24" aria-hidden="true"><path d="M6.6 10.8a15 15 0 0 0 6.6 6.6l2.2-2.2c.3-.3.7-.4 1-.2 1.1.4 2.3.6 3.6.6.6 0 1 .4 1 1V20c0 .6-.4 1-1 1A17 17 0 0 1 3 4c0-.6.4-1 1-1h3.5c.6 0 1 .4 1 1 0 1.3.2 2.5.6 3.6.1.3 0 .7-.2 1z"/></svg>
        555-014-2200
      </li>
      <li>
        <svg viewBox="0 0 24 24" aria-hidden="true"><path d="M2 8c0-2 4-4 10-4s10 2 10 4v2h-5V8H7v2H2z"/><path d="M5 20l2-8h10l2 8z"/><circle cx="12" cy="16" r="2" fill="#1e1e1e"/></svg>
        555-014-2200
      </li>
      <li>
        <svg viewBox="0 0 24 24" aria-hidden="true"><path d="M2 5h20v14H2z M4 7v.4l8 6 8-6V7l-8 6z" fill-rule="evenodd"/></svg>
        info@rdg-build.com
      </li>
      <li>
        <svg viewBox="0 0 24 24" aria-hidden="true" fill="none" stroke="#7dc84a" stroke-width="1.6"><circle cx="12" cy="12" r="10"/><ellipse cx="12" cy="12" rx="4.5" ry="10"/><path d="M2 12h20M4 7h16M4 17h16M12 2v20"/></svg>
        www.<span class="hl">rdg-build</span>.com
      </li>
    </ul>

    <div class="brand brand-back">
      <span class="brand-mark"></span>
      <span class="brand-name">RIDGELINE BUILD</span>
    </div>
  </section>
</body>
</html>
```